International Clinical Software Company needs a new business card design

We are looking for a new business card design for our company that has recently expanded into the UK market, making us a multinational company.
After having rebranded our website and produced a new style guide, we are looking for a business card that is creative and attention grabbing, while being consistent with the style and colour scheme used on the new website, www.plumvora.example
We produce care management technology for the aged care market, but the main aspect we aim to communicate is the human element of our software, and the way it assists in providing better care for aged people, and stronger relationships between aged people and the staff that care for them.
Our current business card is a dark green with gold text, which makes the text quite difficult to read, not very aesthetically appealing and the colour scheme looks quite dated.
We would like something fresh and modern, that can still be colourful but doesn't use large blocks of dark colour, and uses the colours within our logo.
Something tying in with the leaves that are used in our logo could work quite nicely, along with the Autumn/Fall colours of soft greens, yellows and reds (also in our existing logo). However also happy to look at fresh, completely out of the box ideas we may not have yet considered.
Target Market(s)
The people that receive this business card work in the aged card or health industry and are either corporate/management level staff or clinical (Registered Nurses, care workers etc.)
Industry/Entity Type
Health Product
Contact Information for Business Card
Company Name - BrindlewayCare
Company locations: United Kingdom, Australia, New Zealand
Staff Details:
Staff name: Derek Mallow
Staff job title: Executive Chairman
Staff email: d.mallow@plumvora.example
Office phone number: 01742 918576
Font styles to use
Other font styles liked:
- Calibri
Requirements
Must have
- Must include the BrindlewayCare brand name in it's current font
- Must include logo (3 leaves in gold circle)
- Must include Business Card Details
Nice to have
- Elements of gold
- White space
- Something autumn themed but not too cliched
Should not have
- No blue - used by a major competitor and we would like to differentiate from them
- Large blocks of dark green colour (the green that appears in our leaves on the logo on our current business card is the background colour and it is far too dark)

```html
<!DOCTYPE html>
<html lang="en">
<head>
<meta charset="utf-8">
<title>BrindlewayCare Business Card</title>
<link rel="stylesheet" href="https://fonts.googleapis.com/css2?family=Open+Sans:wght@400;600;700&display=swap">
<style>
  :root {
    --page-bg: #efedea;
    --ink: #1e1a14;
    --white: #ffffff;
    --brand-tan: #a8916f;
    --leaf-orange: #ec8a1c;
    --leaf-amber: #f3b52c;
    --leaf-yellow: #f6dc6a;
    --soft-mint: #cdeccf;
    --soft-cream: #f4f3c2;
    --card-shadow: rgba(60, 40, 10, 0.22);
  }
  * { box-sizing: border-box; margin: 0; padding: 0; }
  html, body {
    width: 1200px;
    height: 900px;
    overflow: hidden;
    background: var(--page-bg);
    font-family: "Open Sans", Calibri, Arial, sans-serif;
    color: var(--ink);
  }
  .canvas { position: relative; width: 1200px; height: 900px; }

  .card {
    position: absolute;
    overflow: hidden;
    box-shadow: 0 6px 18px var(--card-shadow);
  }
  .card--front { left: 238px; top: 58px; width: 555px; height: 347px; }
  .card--back  { left: 457px; top: 518px; width: 560px; height: 344px; }

  .autumn-backdrop {
    position: absolute;
    inset: 0;
    background:
      radial-gradient(ellipse 45% 60% at 12% 70%, rgba(246, 214, 90, 0.95), transparent 70%),
      radial-gradient(ellipse 40% 45% at 30% 15%, rgba(236, 120, 30, 0.85), transparent 70%),
      radial-gradient(ellipse 30% 40% at 98% 10%, rgba(236, 130, 30, 0.9), transparent 70%),
      radial-gradient(ellipse 45% 45% at 70% 20%, var(--soft-mint), transparent 75%),
      linear-gradient(100deg, var(--leaf-orange) 0%, var(--leaf-amber) 30%, #e9cf6a 55%, var(--soft-cream) 100%);
  }
  .card--back .autumn-backdrop {
    background:
      radial-gradient(ellipse 40% 55% at 15% 70%, rgba(246, 214, 90, 0.95), transparent 70%),
      radial-gradient(ellipse 45% 35% at 40% 8%, rgba(234, 110, 30, 0.85), transparent 70%),
      radial-gradient(ellipse 25% 40% at 100% 15%, rgba(236, 130, 30, 0.8), transparent 70%),
      radial-gradient(ellipse 45% 50% at 72% 25%, var(--soft-mint), transparent 75%),
      linear-gradient(100deg, var(--leaf-orange) 0%, var(--leaf-amber) 28%, #ecd37a 55%, var(--soft-cream) 100%);
  }

  .brand-mark {
    position: absolute;
    display: flex;
    align-items: center;
    gap: 12px;
  }
  .brand-mark__circle { border-radius: 50%; flex: none; }
  .brand-mark__name { font-weight: 600; white-space: nowrap; }

  .card--front .brand-mark { left: 28px; top: 70px; }
  .card--front .brand-mark__circle {
    width: 48px; height: 48px;
    border: 4px solid var(--white);
  }
  .card--front .brand-mark__name { color: var(--white); font-size: 26px; }

  .contact {
    position: absolute;
    right: 33px;
    top: 188px;
    text-align: right;
    font-size: 14.5px;
    line-height: 20px;
  }
  .contact__name { font-size: 18.5px; font-weight: 700; line-height: 24px; }
  .contact__title { margin-bottom: 14px; }
  .contact__email { display: flex; justify-content: flex-end; align-items: center; gap: 9px; margin-bottom: 14px; }
  .contact__email svg { width: 12px; height: 12px; }

  .card--back .brand-mark {
    right: 36px;
    top: 150px;
    flex-direction: column;
    align-items: center;
    gap: 10px;
  }
  .card--back .brand-mark__circle {
    width: 64px; height: 64px;
    border: 3px solid var(--brand-tan);
  }
  .card--back .brand-mark__name {
    color: var(--brand-tan);
    font-size: 38px;
    font-weight: 400;
    letter-spacing: 0.5px;
  }
</style>
</head>
<body>
<main class="canvas">
  <section class="card card--front">
    <div class="autumn-backdrop" role="img" aria-label="Soft-focus autumn maple leaves in orange and yellow"></div>
    <div class="brand-mark">
      <span class="brand-mark__circle"></span>
      <span class="brand-mark__name">BrindlewayCare</span>
    </div>
    <div class="contact">
      <p class="contact__name">Derek Mallow</p>
      <p class="contact__title">Executive Chairman</p>
      <p class="contact__email">d.mallow@plumvora.example
        <svg viewBox="0 0 24 24" aria-hidden="true"><path fill="currentColor" d="M6.6 10.8a15.1 15.1 0 0 0 6.6 6.6l2.2-2.2a1 1 0 0 1 1-.25 11.4 11.4 0 0 0 3.6.57 1 1 0 0 1 1 1V20a1 1 0 0 1-1 1A17 17 0 0 1 3 4a1 1 0 0 1 1-1h3.5a1 1 0 0 1 1 1c0 1.25.2 2.45.57 3.6a1 1 0 0 1-.25 1z"/></svg>
      </p>
      <p>United Kingdom, Australia</p>
      <p>New Zealand</p>
    </div>
  </section>

  <section class="card card--back">
    <div class="autumn-backdrop" role="img" aria-label="Soft-focus autumn maple leaves in orange and yellow"></div>
    <div class="brand-mark">
      <span class="brand-mark__circle"></span>
      <span class="brand-mark__name">BrindlewayCare</span>
    </div>
  </section>
</main>
</body>
</html>
```